Business card design Needed for new logo / Construction business, home extensions and new builds

We need a business card design using our new logo files which i will attach to this project :)

We are a small construction business specialising in home extensions, new builds and property development. We are very ambitious and would appreciate professional and elegant designs for our new business card.

Very serious about using the services on MakerQuarry and recently acquired our new logo from here :)

Please get involved, i will feedback when i can as i am very busy but can respond daily, thanks

Target Market(s)

People that want to build onto their houses, new building developments or adding too their existing property

Industry/Entity Type

Construction

Contact Information for Business Card

Renwick Tolliver Construction, Lionel Ashby (Managing Director), Tel 07822254961, email - info@renwick-tolliver, www.renwick-tolliver.co.uk

Colors

Designer to choose colors to be used in the design.

Requirements
Must have
• I like a deep grey on the back please. A lot of you have provided black from and back, try mixing things up a little. The black looks cool 😎 Thanks

```html
<!DOCTYPE html>
<html lang="en">
<head>
<meta charset="utf-8">
<title>Renwick Tolliver Construction – Business Card</title>
<link rel="stylesheet" href="https://fonts.googleapis.com/css2?family=Open+Sans:wght@400;600;700&family=Cinzel:wght@500&display=swap">
<style>
  :root {
    --page: #2b2b2e;
    --card: #1d1d20;
    --card-back: #232326;
    --gold: #e9ad2a;
    --gold-light: #f6d27a;
    --gold-dark: #a8771a;
    --silver: #d9dadc;
    --silver-dark: #8d8f93;
    --white: #f4f4f4;
  }
  * { margin: 0; padding: 0; box-sizing: border-box; }
  html, body { width: 1200px; height: 780px; overflow: hidden; }
  body {
    background: var(--page);
    font-family: "Open Sans", sans-serif;
    display: flex;
    align-items: center;
    justify-content: center;
    gap: 40px;
  }
  .card {
    position: relative;
    width: 560px;
    height: 320px;
    border-radius: 26px;
    overflow: hidden;
    border-bottom: 4px solid var(--gold);
    border-left: 2px solid var(--gold);
    box-shadow: 0 18px 40px rgba(0,0,0,.5);
  }

  /* Back */
  .card-back { background: var(--card-back); }
  .back-pattern {
    position: absolute; inset: 0;
    background: linear-gradient(160deg, #3a3a3e 0%, #262629 45%, #1b1b1e 100%);
  }
  .back-brand {
    position: absolute; right: 28px; top: 118px;
    display: flex; align-items: center; gap: 6px;
    font-family: "Cinzel", serif; font-weight: 500;
    font-size: 9px; letter-spacing: .5px; color: var(--gold);
  }
  .back-brand .dot { width: 8px; height: 8px; background: var(--gold); }

  /* Front */
  .card-front { background: var(--card); }
  .brand {
    position: absolute; left: 34px; top: 118px; width: 200px;
    display: flex; flex-direction: column; align-items: center; gap: 10px;
  }
  .brand-mark { width: 22px; height: 22px; background: var(--gold); }
  .brand-name {
    font-family: "Cinzel", serif; font-weight: 500;
    font-size: 19px; line-height: 1.25; text-align: center;
    color: var(--gold); letter-spacing: 1px;
  }
  .divider {
    position: absolute; left: 262px; top: 36px;
    width: 2px; height: 190px; background: var(--white);
  }
  .contact {
    position: absolute; left: 286px; top: 30px; color: var(--white);
  }
  .person-name { font-size: 28px; font-weight: 700; line-height: 1.1; color: var(--silver); }
  .person-name .surname { color: var(--gold); }
  .person-role { font-size: 13px; font-weight: 600; margin-top: 2px; }
  .address { font-size: 13px; line-height: 1.4; margin-top: 14px; }
  .details { list-style: none; margin-top: 14px; font-size: 13px; line-height: 1.55; }
  .details li { display: flex; align-items: center; gap: 8px; }
  .details svg { width: 12px; height: 12px; flex: none; }
  .band {
    position: absolute; left: 0; right: 0; bottom: 26px; height: 22px;
    background: linear-gradient(90deg, var(--gold-dark) 0%, var(--gold) 25%, var(--gold-light) 45%, var(--gold) 58%, var(--silver-dark) 66%, var(--silver) 82%, #ffffff 90%, var(--silver) 100%);
  }
  .band-mark {
    position: absolute; left: 362px; bottom: 21px;
    width: 30px; height: 30px; background: var(--card);
    border: 2px solid var(--silver);
  }
</style>
</head>
<body>

  <section class="card card-back" aria-label="Card back">
    <div class="back-pattern" role="img" aria-label="Repeating brand monogram pattern fading from grey to black"></div>
    <div class="back-brand"><span class="dot"></span>Renwick Tolliver Construction</div>
  </section>

  <section class="card card-front" aria-label="Card front">
    <div class="brand">
      <span class="brand-mark"></span>
      <p class="brand-name">Renwick Tolliver Construction</p>
    </div>

    <div class="divider"></div>

    <div class="contact">
      <h1 class="person-name">Lionel <span class="surname">Ashby</span></h1>
      <p class="person-role">Managing Director</p>
      <p class="address">Harlow Lane, Eastfield<br>Westbury, WB4 7QT</p>
      <ul class="details">
        <li>
          <svg viewBox="0 0 24 24"><path fill="#e9ad2a" d="M6.6 10.8a15 15 0 0 0 6.6 6.6l2.2-2.2a1 1 0 0 1 1-.25 11.4 11.4 0 0 0 3.6.57 1 1 0 0 1 1 1V20a1 1 0 0 1-1 1A17 17 0 0 1 3 4a1 1 0 0 1 1-1h3.5a1 1 0 0 1 1 1c0 1.25.2 2.45.57 3.57a1 1 0 0 1-.25 1z"/></svg>
          0782 225 4961
        </li>
        <li>
          <svg viewBox="0 0 24 24"><rect x="2" y="5" width="20" height="14" rx="2" fill="#e9ad2a"/><path d="M3 6l9 7 9-7" stroke="#1d1d20" stroke-width="2" fill="none"/></svg>
          info@renwick-tolliver.co.uk
        </li>
        <li>
          <svg viewBox="0 0 24 24"><circle cx="12" cy="12" r="10" fill="#e9ad2a"/><path d="M2 12h20M12 2c3 3 3 17 0 20M12 2c-3 3-3 17 0 20" stroke="#1d1d20" stroke-width="1.5" fill="none"/></svg>
          www.renwick-tolliver.co.uk
        </li>
      </ul>
    </div>

    <div class="band"></div>
    <div class="band-mark"></div>
  </section>

</body>
</html>
```